Law Firm Advertising Design Needed

Law Office of Dalmer K Quoss provides legal services to businesses and individuals who have been or are being injured. Our main practice area is personal injury (car accidents, wrongful death, premises liability), but we are looking for an ad that highlights a lesser known area of our practice - insurance company bad faith and breach of contract.

This ad will be placed in 8 1/2" x 11" format in a local neighborhood directory. It will also be placed in a smaller format (to be determined) in the local newspaper of a region of Arizona that has recently lost a considerable number of homes and people to wildfire.

We want to convey through the ad that our firm is available to help if their insurance company is not paying a legitimate claim or not paying enough for their claim.

Because of the tragic nature of the events in Velmont, we would like to avoid images of fire or anything resembling fire. However, the ad should capture the attention of individuals who are struggling through an insurance claim with all the stacks of paperwork and frustrated with unresponsive adjusters and unreasonably low offers.

The design should convey a feeling of safety, security and being taken care of.

Information that must be included in the ad are: the firm name (Law Office of Dalmer K Quoss), address (47390 N 18th Street, Ste 506, Phoenix, AZ 85044), the phone number (602-514-7730) and the fact that we have mobile offices available to assist in your area.

An example of text that has been used in the past is here:
"If your own insurance company is refusing to pay what you are owed on a claim, call the Law Office of Dalmer K Quoss. We fight for you by examining the reasons your insurance carrier is denying or making an insufficient offer on the claim; updating and correcting claim documentation; making a new demand and filing a lawsuit if necessary. Whether it's a simple misunderstanding or something more complicated, we can help!

Here are a few of the kinds of claims we handle:
- Hit and Run or Uninsured driver claims
- Fire, flood and property loss
- Life insurance benefits
- Health insurance claims
- Catastrophic losses
- Business insurance
- Wrongful Death Benefits

Our attorneys are available to help you cut through the nonsense. Call to make an appointment for a free consultation with an attorney today. "

An example of a previous ad for car accident services is attached for reference.
Updates

Hi Everyone,

The main lawyer involved in the decision making process has been giving me some feedback in general on the designs that I thought I would pass along.  He does not want the name of the law firm to be the first thing you notice when you look at the ad. Try to keep that small and possibly to the bottom of the ad. The phone number should be rather large, but the address should be rather small (we are required by the Lawyers' Guild to include our address, but we don't want our location to limit the location of our clients because our mobile offices can travel to them).  He would prefer that the logo either not be included or be not a significant part of the ad.

                                   

Thanks!  I will continue providing individual feedback to ads received. 

Target Market(s)

Low to middle income residents of the State of Arizona with little or no college education

Industry/Entity Type

Insurance

```html
<!DOCTYPE html>
<html lang="en">
<head>
<meta charset="utf-8">
<title>We Fight For You – Law Office of Dalmer K Quoss</title>
<link href="https://fonts.googleapis.com/css2?family=Cinzel:wght@600;700&family=EB+Garamond:ital,wght@0,400;0,600;0,700;1,400;1,600&display=swap" rel="stylesheet">
<style>
  :root {
    --page-bg: #ececec;
    --navy: #1b2a3a;
    --navy-deep: #152230;
    --teal: #14506a;
    --teal-light: #1c6785;
    --text: #e9eef2;
    --text-soft: #c9d3db;
    --tick: #8fd22b;
    --photo-light: #b9d2e6;
    --photo-dark: #2a3a4a;
  }
  * { margin: 0; padding: 0; box-sizing: border-box; }
  html, body { width: 1200px; height: 1000px; overflow: hidden; }
  body { background: var(--page-bg); position: relative; font-family: "EB Garamond", Georgia, serif; color: var(--text); }

  .flyer { position: absolute; left: 295px; top: 103px; width: 612px; height: 792px; background: var(--navy); overflow: hidden; }
  .band { position: absolute; left: 0; width: 100%; background: linear-gradient(180deg, var(--teal-light), var(--teal) 40%, #0f4158); box-shadow: 0 3px 6px rgba(0,0,0,.45); z-index: 2; }

  .headline-band { top: 0; height: 69px; }
  .headline { font-family: "Cinzel", "Times New Roman", serif; font-weight: 700; font-size: 51px; text-align: center; line-height: 78px; color: #fff; letter-spacing: 0.5px; }

  .intro { position: absolute; top: 72px; left: 0; width: 100%; height: 260px; background: linear-gradient(180deg, var(--navy) 0%, #1e3042 60%, var(--navy-deep) 100%); padding: 16px 25px 0 24px; }
  .intro-copy { font-size: 15.2px; line-height: 18.3px; text-align: justify; color: var(--text); }
  .intro-copy strong { font-weight: 700; color: #fff; }
  .availability { margin-top: 12px; font-style: italic; font-size: 15.5px; padding-left: 2px; color: var(--text); }
  .availability strong { font-weight: 700; letter-spacing: 1px; }
  .claims { display: flex; margin-top: 9px; padding-left: 8px; }
  .claims ul { list-style: none; font-size: 15px; line-height: 18.2px; }
  .claims ul:first-child { width: 330px; }
  .claims li { display: flex; align-items: center; }
  .claims li svg { width: 12px; height: 12px; margin-right: 8px; flex: none; }
  .claims .more { font-style: italic; padding-left: 20px; }

  .appointment-band { top: 332px; height: 83px; text-align: center; }
  .appointment-title { font-family: "Cinzel", serif; font-weight: 700; font-size: 31px; color: #fff; margin-top: 11px; line-height: 36px; }
  .appointment-sub { font-size: 19px; font-style: italic; font-weight: 600; line-height: 22px; }
  .appointment-sub b { font-style: normal; font-family: "Cinzel", serif; font-size: 16px; font-weight: 700; }

  .photo { position: absolute; top: 415px; left: 0; width: 100%; height: 232px; background: radial-gradient(ellipse at 45% 45%, #d8e4ec 0%, var(--photo-light) 35%, #6f8fae 65%, var(--photo-dark) 100%); }

  .firm-band { top: 647px; height: 48px; }
  .firm-name { font-family: "Cinzel", serif; font-weight: 700; font-size: 21px; line-height: 50px; padding-left: 18px; color: #fff; }

  .footer { position: absolute; top: 695px; left: 0; width: 100%; height: 97px; background: linear-gradient(180deg, #22344a, var(--navy-deep)); padding: 12px 0 0 18px; }
  .address { font-size: 11.5px; color: var(--text-soft); }
  .call { font-family: "Cinzel", serif; font-weight: 700; font-size: 25px; color: #fff; margin-top: 3px; letter-spacing: 0.5px; }
  .mobile { font-size: 12.5px; font-style: italic; color: var(--text-soft); margin-top: 1px; }
  .web { position: absolute; right: 45px; bottom: 12px; font-family: Arial, sans-serif; font-size: 11.5px; color: #fff; }

  .brand { position: absolute; left: 452px; top: 640px; display: flex; align-items: center; gap: 8px; z-index: 3; }
  .brand-mark { width: 14px; height: 14px; background: #fff; }
  .brand-name { font-family: "EB Garamond", serif; font-size: 26px; font-weight: 600; color: #fff; line-height: 1; }
</style>
</head>
<body>
  <main class="flyer">
    <header class="band headline-band">
      <h1 class="headline">WE FIGHT FOR YOU</h1>
    </header>

    <section class="intro">
      <p class="intro-copy">If your own insurance company is refusing to pay what you are owed on a claim, call the Law Office of Dalmer K Quoss. <strong>We fight for you</strong> by examining the reasons your insurance carrier is denying or making an insufficient offer on the claim; updating and correcting claim documentation; making a new demand and filing a lawsuit if necessary. Whether it's a simple misunderstanding or something more complicated, <strong>WE CAN HELP!</strong></p>
      <p class="availability"><strong>OUR ATTORNEYS ARE AVAILABLE</strong> to help you cut through the nonsense.</p>
      <div class="claims">
        <ul>
          <li><svg viewBox="0 0 12 12"><path d="M1 6.5 L4.5 10 L11 1.5" fill="none" stroke="var(--tick)" stroke-width="2"/></svg>Hit and Run or Uninsured driver claims</li>
          <li><svg viewBox="0 0 12 12"><path d="M1 6.5 L4.5 10 L11 1.5" fill="none" stroke="var(--tick)" stroke-width="2"/></svg>Fire, flood and property loss</li>
          <li><svg viewBox="0 0 12 12"><path d="M1 6.5 L4.5 10 L11 1.5" fill="none" stroke="var(--tick)" stroke-width="2"/></svg>Life insurance benefits</li>
          <li><svg viewBox="0 0 12 12"><path d="M1 6.5 L4.5 10 L11 1.5" fill="none" stroke="var(--tick)" stroke-width="2"/></svg>Health insurance claims</li>
        </ul>
        <ul>
          <li><svg viewBox="0 0 12 12"><path d="M1 6.5 L4.5 10 L11 1.5" fill="none" stroke="var(--tick)" stroke-width="2"/></svg>Catastrophic losses</li>
          <li><svg viewBox="0 0 12 12"><path d="M1 6.5 L4.5 10 L11 1.5" fill="none" stroke="var(--tick)" stroke-width="2"/></svg>Business insurance</li>
          <li><svg viewBox="0 0 12 12"><path d="M1 6.5 L4.5 10 L11 1.5" fill="none" stroke="var(--tick)" stroke-width="2"/></svg>Wrongful Death Benefits</li>
          <li class="more">and many more</li>
        </ul>
      </div>
    </section>

    <section class="band appointment-band">
      <h2 class="appointment-title">CALL TO MAKE AN APPOINTMENT</h2>
      <p class="appointment-sub">for <b>A FREE CONSULTATION</b> with an attorney today!</p>
    </section>

    <div class="photo" role="img" aria-label="Photo of hands holding a smartphone and tapping the screen, in a light blue shirt"></div>

    <section class="band firm-band">
      <p class="firm-name">LAW OFFICE OF DALMER K QUOSS</p>
    </section>

    <div class="brand">
      <span class="brand-mark"></span>
      <span class="brand-name">Quoss Law</span>
    </div>

    <footer class="footer">
      <p class="address">Law Office of Dalmer K Quoss | 47390 N 18th Street, Ste 506, Phoenix, AZ 85044</p>
      <p class="call">CALL US NOW!&nbsp; 602-514-7730</p>
      <p class="mobile">We have mobile offices available to assist in your area.</p>
      <p class="web">www.quosslaw.com</p>
    </footer>
  </main>
</body>
</html>
```